Modern card design needed for building development company

We are looking for a sharp modern new look for our business cards.
We are a New Zealand based company called TKR Ventures NZ LTD that specialises in subdividing large sections, housing and commercial buildings.
We have attached a photo of the current logo and would like to see it improved somehow as it looks a bit dated.
We are open to any colours.

Target Market(s)

Investors, Property buyers

Industry/Entity Type

Investment

Contact Information for Business Card

TKR VENTURES NZ LTD
www.tkrventuresnz.co.nz

Damon Whitcombe
Phone +64 21 938 104
Email dpwhitcombe@korumail.co.nz

Font styles to use
Serif
Sans Serif

Colors
0792cd
33a6d7
85cae6
6b449b
886aae
f04a50
ec1f27
f37122
f68d4d

Requirements
Must have
• Please try and make the logo more modern or if you have a similar one we would like to see it.

```html
<!DOCTYPE html>
<html lang="en">
<head>
<meta charset="utf-8">
<title>TKR Ventures NZ LTD – Business Card</title>
<link rel="stylesheet" href="https://fonts.googleapis.com/css2?family=Cinzel:wght@500&family=Open+Sans:wght@400;700&display=swap">
<style>
  :root {
    --canvas-bg: #e9e7e3;
    --card-bg: #2a2a2c;
    --accent-yellow: #eeab14;
    --accent-grey: #8e8e8e;
    --text-light: #c9c9c9;
    --text-muted: #a9a9a9;
  }
  * { box-sizing: border-box; margin: 0; padding: 0; }
  html, body {
    width: 1200px;
    height: 900px;
    overflow: hidden;
    background: var(--canvas-bg);
  }
  .canvas {
    width: 1200px;
    height: 900px;
    display: flex;
    align-items: center;
    justify-content: center;
    gap: 40px;
  }
  .card {
    position: relative;
    width: 540px;
    height: 310px;
    background: var(--card-bg);
    overflow: hidden;
    box-shadow: 0 10px 24px rgba(0,0,0,0.18);
  }

  /* Front */
  .brand-lockup {
    position: absolute;
    top: 50%;
    left: 50%;
    transform: translate(-50%, -50%);
    display: flex;
    flex-direction: column;
    align-items: center;
    gap: 14px;
  }
  .brand-mark {
    width: 34px;
    height: 34px;
    background: var(--accent-yellow);
  }
  .brand-name {
    font-family: "Cinzel", serif;
    font-weight: 500;
    color: var(--text-light);
    text-align: center;
    line-height: 1.1;
    letter-spacing: 1px;
    white-space: nowrap;
  }
  .brand-name .line-main { display: block; font-size: 36px; }
  .brand-name .line-sub { display: block; font-size: 15px; letter-spacing: 4px; margin-top: 6px; }

  /* Back */
  .back-brand {
    position: absolute;
    right: 40px;
    top: 40px;
    display: flex;
    align-items: center;
    gap: 8px;
    font-family: "Cinzel", serif;
    font-weight: 500;
    font-size: 15px;
    color: var(--accent-yellow);
    letter-spacing: 1px;
  }
  .back-brand .brand-mark { width: 16px; height: 16px; }
  .contact-name {
    position: absolute;
    left: 40px;
    top: 90px;
    font-family: "Open Sans", sans-serif;
    font-weight: 700;
    font-size: 17px;
    color: var(--accent-yellow);
    letter-spacing: 0.2px;
  }
  .contact-list {
    position: absolute;
    left: 40px;
    top: 146px;
    list-style: none;
    font-family: "Open Sans", sans-serif;
    font-size: 13px;
    color: var(--text-muted);
    line-height: 20px;
    z-index: 2;
  }
  .contact-list li { display: flex; align-items: center; gap: 8px; white-space: nowrap; }
  .contact-list svg { width: 11px; height: 11px; flex: none; }
  .wave {
    position: absolute;
    left: 0;
    top: 0;
    width: 540px;
    height: 310px;
    z-index: 1;
  }
</style>
</head>
<body>
<main class="canvas">

  <section class="card card-front" aria-label="Card front">
    <div class="brand-lockup">
      <span class="brand-mark" aria-hidden="true"></span>
      <h1 class="brand-name">
        <span class="line-main">TKR VENTURES</span>
        <span class="line-sub">NZ LTD</span>
      </h1>
    </div>
  </section>

  <section class="card card-back" aria-label="Card back">
    <div class="back-brand">
      <span class="brand-mark" aria-hidden="true"></span>
      <span>TKR VENTURES</span>
    </div>

    <h2 class="contact-name">DAMON WHITCOMBE</h2>

    <ul class="contact-list">
      <li>
        <svg viewBox="0 0 12 12" aria-hidden="true"><rect x="3" y="0.8" width="6" height="10.4" rx="1" fill="none" stroke="currentColor" stroke-width="1.2"/><circle cx="6" cy="9.4" r="0.7" fill="currentColor"/></svg>
        +64 21 938 104
      </li>
      <li>
        <svg viewBox="0 0 12 12" aria-hidden="true"><rect x="0.6" y="2.4" width="10.8" height="7.4" fill="currentColor"/><path d="M0.6 2.6 L6 7 L11.4 2.6" fill="none" stroke="#2a2a2c" stroke-width="1"/></svg>
        dpwhitcombe@korumail.co.nz
      </li>
      <li>
        <svg viewBox="0 0 12 12" aria-hidden="true"><path d="M5 7 L7 5" stroke="currentColor" stroke-width="1.2"/><rect x="5.6" y="0.8" width="4" height="5.6" rx="2" transform="rotate(45 7.6 3.6)" fill="none" stroke="currentColor" stroke-width="1.2"/><rect x="2.4" y="5.6" width="4" height="5.6" rx="2" transform="rotate(45 4.4 8.4)" fill="none" stroke="currentColor" stroke-width="1.2"/></svg>
        www.tkrventuresnz.co.nz
      </li>
    </ul>

    <svg class="wave" viewBox="0 0 540 310" aria-hidden="true">
      <path d="M0,256 C160,282 300,246 370,196 C430,154 485,142 540,140 L540,154 C485,156 430,168 370,210 C300,260 160,298 0,272 Z" fill="var(--accent-grey)"/>
      <path d="M0,272 C160,298 300,260 370,210 C430,168 485,156 540,154 L540,310 L0,310 Z" fill="var(--accent-yellow)"/>
    </svg>
  </section>

</main>
</body>
</html>
```